Yacht, Boats, Watersports company needs a redesign of business card

Hello Designers!
We are a Boat dealership company that sells fun in the water, we sell boats, Yachts, Kayaks and also yacht WaterSport toys. We are looking to redesign our business cards in to something a little bit more sophisticated. in a way that we can make better use of our company colors. I'm attaching a zipped file containing the company 3 sets of company logo which one is an horizontal another one is a vertical and also a chromed 3d logo. Also is included two set of business cards that we use and also some designs that i think it's interesting. We use PMS 2026c Orange and PMS 7687C Blue. I would like to see at least two different options with the orange as accent and also using blue as an accent color. It's really important for the business cards to have a font option and size that is legible to most people. Our current website is wwww.coralpennant.com. Please visit if you want to have a better feeling of the Boat dealership
You can send Single sided or double side options. We are now using single sided but we may be open for a double side option if we really like the design.
Target Market(s)
Marine, boat sales, yacht sales, water toys sales/
Contact Information for Business Card
Name: Dale Whitcombe
Address: 212 North Fenwick Lane,
Dania Beach, FL 33004
Phone: 954-731-8842
Fax: 954:731-8843
Cell: 954-382-1490
Email: dw@coralpennant.com
Website: coralpennant.com
Requirements
Must have
- the current information of the business card provided.
logo
use the PMS Colors
Nice to have
- a touch of elegance and sophistication but simple
Should not have
- should not have any typography that is hard to read, the card should be simple but yet sophisticated.

```html
<!DOCTYPE html>
<html lang="en">
<head>
<meta charset="utf-8">
<title>Coral Pennant – Business Card</title>
<link href="https://fonts.googleapis.com/css2?family=Michroma&family=Roboto:wght@400&display=swap" rel="stylesheet">
<style>
  :root {
    --blue: #0e4679;
    --orange: #f26430;
    --white: #ffffff;
    --backdrop: #b8b8b8;
  }
  html, body {
    margin: 0;
    padding: 0;
    width: 1200px;
    height: 801px;
    overflow: hidden;
    background: var(--backdrop);
  }
  .canvas {
    position: relative;
    width: 1200px;
    height: 801px;
  }
  .card {
    position: absolute;
    top: 274px;
    width: 443px;
    height: 263px;
    overflow: hidden;
  }
  .card--front {
    left: 153px;
    background: var(--blue);
  }
  .card--back {
    left: 625px;
    background: var(--white);
  }
  .accent-band {
    position: absolute;
    inset: 0;
  }
  .holder-name {
    position: absolute;
    left: 17px;
    top: 30px;
    margin: 0;
    font-family: "Michroma", sans-serif;
    font-size: 12.5px;
    letter-spacing: 0.5px;
    color: var(--orange);
    text-transform: uppercase;
    font-weight: 400;
  }
  .address {
    position: absolute;
    left: 17px;
    top: 112px;
    margin: 0;
    font-family: "Roboto", sans-serif;
    font-style: normal;
    font-size: 13px;
    line-height: 15.6px;
    color: var(--white);
  }
  .contact-list {
    position: absolute;
    left: 17px;
    top: 157px;
    margin: 0;
    padding: 0;
    list-style: none;
    font-family: "Roboto", sans-serif;
    font-size: 13px;
    line-height: 15.6px;
    color: var(--white);
  }
  .contact-list li {
    display: flex;
    align-items: center;
    gap: 6px;
  }
  .contact-list svg {
    width: 11px;
    height: 11px;
    flex: none;
    fill: var(--orange);
  }
  .front-wordmark {
    position: absolute;
    left: 215px;
    top: 100px;
    width: 200px;
    margin: 0;
    text-align: center;
    font-family: "Michroma", sans-serif;
    font-size: 20px;
    line-height: 30px;
    color: var(--white);
    font-weight: 400;
  }
  .brand {
    position: absolute;
    left: 0;
    right: 0;
    top: 116px;
    display: flex;
    justify-content: center;
    align-items: center;
    gap: 10px;
  }
  .brand-dot {
    width: 18px;
    height: 18px;
    border-radius: 50%;
    background: var(--orange);
  }
  .brand-name {
    margin: 0;
    font-family: "Michroma", sans-serif;
    font-size: 17px;
    letter-spacing: 0.5px;
    color: var(--blue);
    font-weight: 400;
  }
</style>
</head>
<body>
<main class="canvas">
  <section class="card card--front">
    <svg class="accent-band" viewBox="0 0 443 263" width="443" height="263" aria-hidden="true">
      <polygon points="176,263 443,55 443,263" fill="var(--orange)"/>
    </svg>
    <h1 class="holder-name">Dale Whitcombe</h1>
    <address class="address">212 North Fenwick Lane,<br>Dania Beach, FL 33004</address>
    <ul class="contact-list">
      <li><svg viewBox="0 0 12 12"><path d="M2.5 1 4.5 3 3.5 4.5C4.2 6 5.8 7.6 7.5 8.5L9 7.5 11 9.5 9.5 11C5 10.5 1.5 7 1 2.5Z"/></svg>954-731-8842</li>
      <li><svg viewBox="0 0 12 12"><rect x="3" y="1" width="6" height="3"/><rect x="1" y="4.5" width="10" height="4.5" rx="1"/><rect x="3" y="8" width="6" height="3"/></svg>954:731-8843</li>
      <li><svg viewBox="0 0 12 12"><path d="M3 0.5h6a1 1 0 0 1 1 1v9a1 1 0 0 1-1 1H3a1 1 0 0 1-1-1v-9a1 1 0 0 1 1-1Zm0.5 1.5v7h5V2Z"/></svg>954-382-1490</li>
      <li><svg viewBox="0 0 12 12"><path d="M0.5 2.5h11v7h-11Zm0.8 0.8L6 7l4.7-3.7"/></svg>dw@coralpennant.com</li>
      <li><svg viewBox="0 0 12 12"><path d="M6 0.5a5.5 5.5 0 1 0 0 11 5.5 5.5 0 0 0 0-11Zm0 1.2c.8.8 1.4 2.3 1.5 3.7h-3C4.6 4 5.2 2.5 6 1.7ZM3.4 5.4H1.8a4.3 4.3 0 0 1 2.6-3.3c-.6 1-.9 2.1-1 3.3Zm0 1.2c.1 1.2.4 2.3 1 3.3a4.3 4.3 0 0 1-2.6-3.3Zm1.1 0h3c-.1 1.4-.7 2.9-1.5 3.7-.8-.8-1.4-2.3-1.5-3.7Zm4.1 0h1.6a4.3 4.3 0 0 1-2.6 3.3c.6-1 .9-2.1 1-3.3Zm0-1.2c-.1-1.2-.4-2.3-1-3.3a4.3 4.3 0 0 1 2.6 3.3Z"/></svg>www.coralpennant.com</li>
    </ul>
    <p class="front-wordmark">CORAL<br>PENNANT</p>
  </section>

  <section class="card card--back">
    <div class="brand">
      <span class="brand-dot" aria-hidden="true"></span>
      <p class="brand-name">CORAL PENNANT</p>
    </div>
  </section>
</main>
</body>
</html>
```